Design a Website for an IT Support Company

We are an IT support company that provides commercial IT support and services to small and medium sized businesses. We are in need of a website to be developed for our business.
We would like to work with someone who is either familiar with the IT field, or has developed a website for an IT support company in the past.
Some examples of designs/layouts that we like:
https://www.veldaworks.example/
http://www.marsbyquill.example/
http://817kq.example/
http://www.olbenstructures.example/
http://www.bykq.example/
I have attached a word document that gives a menu system/page layout format that we would like for our website as well as branch office phone numbers. Our logo is also attached that you can use for your design purposes. We currently do not have copy produced for all of the pages outlined in the word document, but would get this done during the project with the selected designer.
We would like the website to be SEO friendly & fully responsive. We would prefer a Wordpress format, however, we are open to HTML formats as well.

```html
<!DOCTYPE html>
<html lang="en">
<head>
<meta charset="utf-8">
<title>Kestrel IT – IT Support &amp; Services</title>
<link href="https://fonts.googleapis.com/css2?family=Raleway:wght@400;500;600;700&family=Play:wght@700&display=swap" rel="stylesheet">
<style>
:root{
  --blue:#1d6fc0;
  --blue-dark:#135aa0;
  --blue-light:#3f8ed8;
  --ink:#222;
  --text:#666;
  --muted:#888;
  --line:#e4e4e4;
  --grey-band:#eef0f2;
  --footer:#111;
  --white:#fff;
}
*{box-sizing:border-box;margin:0;padding:0}
html,body{width:1200px;height:3922px;overflow:hidden;background:var(--white)}
body{font-family:"Raleway",sans-serif;color:var(--text);position:relative}
.heading{font-family:"Play",sans-serif;font-weight:700;color:var(--ink);font-size:38px;text-align:center;letter-spacing:1px}
.heading-rule{width:90px;height:3px;background:var(--blue);margin:14px auto 0}

/* header */
.site-header{position:absolute;top:0;left:0;width:1200px;height:145px;background:var(--white)}
.brand{position:absolute;left:100px;top:34px;display:flex;align-items:center;gap:12px}
.brand-dot{width:44px;height:44px;border-radius:50%;background:var(--blue)}
.brand-name{font-family:"Raleway",sans-serif;font-weight:700;font-size:40px;color:#1b2a3a}
.header-call{position:absolute;right:100px;top:28px;display:flex;align-items:center;gap:10px;font-size:15px;font-weight:700;color:#333}
.header-call .ring{width:34px;height:34px;border:2px solid #333;border-radius:50%;display:flex;align-items:center;justify-content:center}
.main-nav{position:absolute;left:418px;top:94px;display:flex;gap:46px;font-size:13px;font-weight:600;color:#444;letter-spacing:.5px}
.main-nav .active{color:var(--blue)}
.login{position:absolute;left:857px;top:87px;width:104px;height:36px;background:var(--blue);color:#fff;font-size:13px;font-weight:600;display:flex;align-items:center;justify-content:center;gap:6px;border-radius:2px}
.social-top{position:absolute;left:977px;top:84px;display:flex;gap:6px}
.social-top span{width:40px;height:40px;border-radius:50%;background:var(--blue)}
.social-top span:nth-child(3){background:#7a5a44}

/* hero */
.hero{position:absolute;top:145px;left:0;width:1200px;height:520px}
.hero-photo{position:absolute;inset:0;background:linear-gradient(100deg,#8ea2b6 0%,#c3d0dc 40%,#e8e1da 65%,#f1ece6 100%)}
.hero-title{position:absolute;left:100px;top:160px;font-family:"Play",sans-serif;font-size:72px;color:#fff;letter-spacing:5px}
.hero-sub{position:absolute;left:100px;top:262px;font-size:22px;color:#fff}
.btn{display:flex;align-items:center;justify-content:center;background:var(--blue);color:#fff;font-size:14px;font-weight:600;letter-spacing:.5px}
.hero-btn{position:absolute;left:100px;top:318px;width:142px;height:44px}
.hero-arrows{position:absolute;left:1020px;top:472px;display:flex;gap:8px;z-index:2}
.hero-arrows span{width:38px;height:38px;border-radius:50%;background:#666;display:flex;align-items:center;justify-content:center}
.hero-curve{position:absolute;left:0;top:440px}

/* welcome */
.welcome{position:absolute;top:700px;left:0;width:1200px}
.welcome p{width:830px;margin:26px auto 0;text-align:center;font-size:14px;line-height:26px;color:var(--muted)}
.welcome-call{display:flex;justify-content:center;align-items:center;gap:12px;margin-top:24px;font-size:27px;font-weight:700;color:var(--blue)}

/* services */
.services{position:absolute;top:1045px;left:0;width:1200px;height:595px;background:linear-gradient(180deg,var(--blue-dark),var(--blue) 60%,#4f9ad8)}
.services .heading{color:#fff;margin-top:58px}
.service-cards{position:absolute;top:145px;left:100px;display:flex;gap:20px}
.service-card{width:320px;height:376px;background:#fff;text-align:center}
.service-photo{height:210px;position:relative}
.service-photo svg{position:absolute;bottom:-1px;left:0}
.service-card h3{font-size:16px;font-weight:600;color:#333;margin-top:18px;letter-spacing:.5px}
.service-card p{font-size:13px;line-height:22px;color:var(--muted);width:250px;margin:10px auto 0}
.read-more{font-size:12px;font-weight:700;color:var(--blue);margin-top:12px;display:flex;justify-content:center;align-items:center;gap:5px}
.services-pointer{position:absolute;left:571px;top:1639px}

/* why */
.why{position:absolute;top:1700px;left:0;width:1200px}
.why-grid{position:absolute;top:90px;left:100px;width:1000px;display:grid;grid-template-columns:repeat(3,1fr);row-gap:40px}
.why-item{text-align:center;height:215px;padding-top:8px;box-shadow:0 6px 10px -8px rgba(0,0,0,.18)}
.why-icon{height:60px;display:flex;justify-content:center;align-items:center}
.why-item h3{font-size:15px;font-weight:700;color:var(--blue);margin-top:14px;letter-spacing:.5px}
.why-item p{font-size:13px;line-height:24px;color:var(--muted);width:250px;margin:10px auto 0}

/* testimonials */
.testimonials{position:absolute;top:2305px;left:0;width:1200px;height:600px;background:var(--grey-band)}
.testimonials .heading{margin-top:70px}
.quote-mark{position:absolute;font-family:Georgia,serif;font-size:150px;color:var(--blue);line-height:1}
.testimonial{position:absolute;width:470px;text-align:center}
.avatar{width:112px;height:112px;border-radius:50%;border:5px solid #fff;margin:0 auto;background:linear-gradient(#b9c3cc,#8a96a2)}
.testimonial p{font-size:13px;line-height:24px;color:var(--muted);margin-top:20px}
.testimonial .rule{width:170px;height:1px;background:#bbb;margin:18px auto 0}
.testimonial h4{font-size:14px;font-weight:700;color:var(--blue);margin-top:14px}
.testimonial small{display:block;font-size:12px;color:var(--muted);margin-top:6px}
.dots{position:absolute;left:578px;top:515px;display:flex;gap:6px}
.dots span{width:10px;height:10px;border-radius:50%;border:1px solid var(--blue)}
.dots span:first-child{background:var(--blue)}
.testimonials-pointer{position:absolute;left:571px;top:2904px}

/* team */
.team{position:absolute;top:2965px;left:0;width:1200px}
.team-row{position:absolute;top:130px;left:135px;display:flex;gap:58px}
.member{width:190px;text-align:center}
.member-photo{width:190px;height:190px;border-radius:50%;border:4px solid #e8e8e8;background:linear-gradient(#dfe6ec,#b7c3cf)}
.member h3{font-size:14px;font-weight:600;color:#333;margin-top:26px;letter-spacing:.5px}
.member p{font-size:13px;color:var(--muted);margin-top:8px}
.member-social{display:flex;justify-content:center;gap:8px;margin-top:16px}
.member-social span{width:24px;height:24px;border-radius:50%;border:1px solid #ccc}

/* footer */
.footer-curve{position:absolute;top:3420px;left:0}
.site-footer{position:absolute;top:3560px;left:0;width:1200px;height:362px;background:var(--footer);color:#ddd}
.footer-brand{position:absolute;left:100px;top:110px;display:flex;align-items:center;gap:14px}
.footer-brand .brand-dot{width:60px;height:60px}
.footer-brand .brand-name{color:#fff;font-size:50px}
.footer-contact{position:absolute;left:486px;top:50px}
.footer-contact h4,.footer-follow h4{font-size:19px;font-weight:700;color:#fff;letter-spacing:.5px}
.footer-contact .call-here{color:var(--blue-light);font-size:14px;margin-top:18px;display:flex;gap:8px;align-items:center}
.branches{display:grid;grid-template-columns:205px 200px;row-gap:22px;margin-top:16px;font-size:12px;color:#ddd;white-space:nowrap}
.footer-follow{position:absolute;left:932px;top:50px}
.follow-icons{display:flex;gap:14px;margin-top:24px}
.follow-icons span{width:38px;height:38px;border-radius:50%;background:var(--blue)}
.subscribe{position:absolute;left:932px;top:160px;width:168px;height:42px;background:#777;color:#fff;font-size:13px;font-weight:600;display:flex;align-items:center;justify-content:center;letter-spacing:.5px}
.copyright{position:absolute;left:0;width:1200px;top:318px;text-align:center;font-size:11px;color:#ccc}
</style>
</head>
<body>

<header class="site-header">
  <div class="brand"><span class="brand-dot"></span><span class="brand-name">Kestrel IT</span></div>
  <div class="header-call">
    <span class="ring"><svg width="16" height="16" viewBox="0 0 24 24"><path d="M6.6 10.8a15 15 0 006.6 6.6l2.2-2.2c.3-.3.7-.4 1-.2 1.1.4 2.3.6 3.6.6.6 0 1 .4 1 1V20c0 .6-.4 1-1 1A17 17 0 013 4c0-.6.4-1 1-1h3.5c.6 0 1 .4 1 1 0 1.3.2 2.5.6 3.6.1.3 0 .7-.2 1z" fill="#333"/></svg></span>
    <span>CALL US : 555-014-2280</span>
  </div>
  <nav class="main-nav">
    <span class="active">HOME</span><span>SERVICES</span><span>WHY KESTREL IT</span><span>CONTACT</span>
  </nav>
  <div class="login"><svg width="11" height="12" viewBox="0 0 12 12"><circle cx="6" cy="3.5" r="3" fill="#fff"/><path d="M0 12c0-3.5 2.7-5 6-5s6 1.5 6 5z" fill="#fff"/></svg>LOG IN</div>
  <div class="social-top"><span></span><span></span><span></span></div>
</header>

<section class="hero">
  <div class="hero-photo" role="img" aria-label="Smiling support agent wearing a headset in a bright office, colleagues blurred behind"></div>
  <h1 class="hero-title">KESTREL IT</h1>
  <div class="hero-sub">IT Support &amp; Services for Your Business</div>
  <div class="btn hero-btn">READ MORE</div>
  <div class="hero-arrows">
    <span><svg width="12" height="12" viewBox="0 0 12 12"><path d="M8 1L3 6l5 5" stroke="#fff" stroke-width="2" fill="none"/></svg></span>
    <span><svg width="12" height="12" viewBox="0 0 12 12"><path d="M4 1l5 5-5 5" stroke="#fff" stroke-width="2" fill="none"/></svg></span>
  </div>
  <svg class="hero-curve" width="1200" height="80" viewBox="0 0 1200 80">
    <path d="M0 50 Q300 0 1200 30 L1200 80 L0 80 Z" fill="#fff"/>
    <path d="M0 50 Q300 0 1200 30" stroke="#888" stroke-width="5" fill="none"/>
    <path d="M0 58 Q320 12 1200 40" stroke="var(--blue)" stroke-width="8" fill="none"/>
  </svg>
</section>

<section class="welcome">
  <h2 class="heading">Welcome To Kestrel IT</h2>
  <p>We keep small and medium sized businesses running with responsive support, proactive monitoring and honest advice. Our certified engineers plan, secure and manage the systems your team relies on every day, so you can focus on growing your company while we handle the technology behind it, from the help desk to the server room.</p>
  <div class="welcome-call"><svg width="22" height="22" viewBox="0 0 24 24"><path d="M6.6 10.8a15 15 0 006.6 6.6l2.2-2.2c.3-.3.7-.4 1-.2 1.1.4 2.3.6 3.6.6.6 0 1 .4 1 1V20c0 .6-.4 1-1 1A17 17 0 013 4c0-.6.4-1 1-1h3.5c.6 0 1 .4 1 1 0 1.3.2 2.5.6 3.6.1.3 0 .7-.2 1z" fill="currentColor"/></svg>Call Us Now ! 555-014-2280</div>
</section>

<section class="services">
  <h2 class="heading">Our Services</h2>
  <div class="service-cards">
    <article class="service-card">
      <div class="service-photo" role="img" aria-label="Hands reviewing charts on a tablet and papers at a desk" style="background:linear-gradient(135deg,#c9d3dc,#7f93a6)">
        <svg width="320" height="40" viewBox="0 0 320 40"><path d="M0 40 Q160 0 320 40Z" fill="#fff"/></svg></div>
      <h3>DATA</h3>
      <p>Reliable backup, storage and recovery plans that protect every file.</p>
      <div class="read-more">Read More <svg width="11" height="11" viewBox="0 0 12 12"><circle cx="6" cy="6" r="6" fill="currentColor"/><path d="M5 3l3 3-3 3" stroke="#fff" stroke-width="1.6" fill="none"/></svg></div>
    </article>
    <article class="service-card">
      <div class="service-photo" role="img" aria-label="Hand touching a glowing network of connected device symbols" style="background:linear-gradient(135deg,#2c5a86,#8fb5d6)">
        <svg width="320" height="40" viewBox="0 0 320 40"><path d="M0 40 Q160 0 320 40Z" fill="#fff"/></svg></div>
      <h3>CLOUD</h3>
      <p>Flexible hosted platforms that scale smoothly as your business grows.</p>
      <div class="read-more">Read More <svg width="11" height="11" viewBox="0 0 12 12"><circle cx="6" cy="6" r="6" fill="currentColor"/><path d="M5 3l3 3-3 3" stroke="#fff" stroke-width="1.6" fill="none"/></svg></div>
    </article>
    <article class="service-card">
      <div class="service-photo" role="img" aria-label="Call centre agent with a headset at a computer" style="background:linear-gradient(135deg,#d8dee4,#9aa9b6)">
        <svg width="320" height="40" viewBox="0 0 320 40"><path d="M0 40 Q160 0 320 40Z" fill="#fff"/></svg></div>
      <h3>VOICE</h3>
      <p>Clear business phone systems with support whenever your team calls.</p>
      <div class="read-more">Read More <svg width="11" height="11" viewBox="0 0 12 12"><circle cx="6" cy="6" r="6" fill="currentColor"/><path d="M5 3l3 3-3 3" stroke="#fff" stroke-width="1.6" fill="none"/></svg></div>
    </article>
  </div>
</section>
<svg class="services-pointer" width="58" height="30" viewBox="0 0 58 30"><path d="M0 0h58L29 30z" fill="#3d8ad2"/></svg>

<section class="why">
  <h2 class="heading">Why Kestrel IT</h2>
  <div class="why-grid">
    <div class="why-item">
      <div class="why-icon"><svg width="62" height="52" viewBox="0 0 62 52" fill="#666"><circle cx="22" cy="26" r="15"/><circle cx="22" cy="26" r="6" fill="#fff"/><circle cx="48" cy="14" r="9"/><circle cx="48" cy="14" r="3.5" fill="#fff"/><circle cx="48" cy="40" r="8"/><circle cx="48" cy="40" r="3" fill="#fff"/></svg></div>
      <h3>MANAGED IT SERVICES</h3>
      <p>Around the clock monitoring and maintenance that keeps your network healthy and fast.</p>
    </div>
    <div class="why-item">
      <div class="why-icon"><svg width="64" height="42" viewBox="0 0 64 42"><path d="M14 40a12 12 0 010-24 17 17 0 0132-4 13 13 0 014 28z" fill="#666"/></svg></div>
      <h3>CLOUD SERVICES</h3>
      <p>Move email, files and apps to secure hosting you can reach from anywhere.</p>
    </div>
    <div class="why-item">
      <div class="why-icon"><svg width="36" height="46" viewBox="0 0 36 46"><path d="M8 20v-7a10 10 0 0120 0v7" stroke="#666" stroke-width="5" fill="none"/><rect x="2" y="20" width="32" height="24" rx="3" fill="#666"/></svg></div>
      <h3>SECURITY SERVICES</h3>
      <p>Firewalls, antivirus and policies that guard your data against modern threats daily.</p>
    </div>
    <div class="why-item">
      <div class="why-icon"><svg width="64" height="46" viewBox="0 0 64 46" fill="#666"><circle cx="22" cy="13" r="10"/><path d="M2 46c0-14 9-19 20-19s20 5 20 19z"/><circle cx="44" cy="15" r="8" fill="none" stroke="#666" stroke-width="3"/><path d="M44 26c10 0 18 4 18 18H44" fill="none" stroke="#666" stroke-width="3"/></svg></div>
      <h3>IT CONSULTING</h3>
      <p>Practical guidance on budgets, upgrades and projects that match your business goals.</p>
    </div>
    <div class="why-item">
      <div class="why-icon"><svg width="56" height="48" viewBox="0 0 56 48"><rect x="2" y="2" width="52" height="34" rx="3" fill="#666"/><rect x="7" y="7" width="42" height="24" fill="#fff"/><rect x="22" y="36" width="12" height="7" fill="#666"/><rect x="14" y="42" width="28" height="4" fill="#666"/></svg></div>
      <h3>VIRTUALIZATION</h3>
      <p>Run more on fewer servers with efficient virtual machines and simple management.</p>
    </div>
    <div class="why-item">
      <div class="why-icon"><svg width="50" height="46" viewBox="0 0 50 46"><path d="M6 30v-6a19 19 0 0138 0v6" stroke="#666" stroke-width="5" fill="none"/><rect x="2" y="26" width="12" height="18" rx="3" fill="#666"/><rect x="36" y="26" width="12" height="18" rx="3" fill="#666"/></svg></div>
      <h3>HOSTED VOIP</h3>
      <p>Modern voice over IP phones with crisp audio and features for every desk.</p>
    </div>
  </div>
</section>

<section class="testimonials">
  <h2 class="heading">What Our Clients Say</h2>
  <div class="heading-rule"></div>
  <div class="quote-mark" style="left:95px;top:140px">&ldquo;</div>
  <div class="quote-mark" style="left:1020px;top:430px">&rdquo;</div>
  <div class="testimonial" style="left:110px;top:175px">
    <div class="avatar" role="img" aria-label="Portrait of a client"></div>
    <p>They answered every call quickly and solved problems before we even noticed them. Our office has never run so smoothly, and the team explains everything in plain language. We trust them completely with our network and recommend them to any growing business.</p>
    <div class="rule"></div>
    <h4>COMMODI CONSEQ</h4>
    <small>Sed quia non</small>
  </div>
  <div class="testimonial" style="left:620px;top:175px">
    <div class="avatar" role="img" aria-label="Portrait of a client" style="background:linear-gradient(#dfe7ef,#9fb4c8)"></div>
    <p>Moving our company to the cloud felt daunting until this team stepped in. The migration was planned carefully, finished on schedule, and our staff barely felt a thing. Support has been friendly and dependable ever since we signed on.</p>
    <div class="rule"></div>
    <h4>OMNIS ISTE NATU</h4>
    <small>Sed quia non</small>
  </div>
  <div class="dots"><span></span><span></span><span></span></div>
</section>
<svg class="testimonials-pointer" width="58" height="30" viewBox="0 0 58 30"><path d="M0 0h58L29 30z" fill="#eef0f2"/></svg>

<section class="team">
  <h2 class="heading">Meet Our Team</h2>
  <div class="heading-rule"></div>
  <div class="team-row">
    <div class="member"><div class="member-photo" role="img" aria-label="Portrait of a support team member with a headset"></div><h3>BEATAE VITAE</h3><p>Ut enim ad minima veniam</p><div class="member-social"><span></span><span></span><span></span></div></div>
    <div class="member"><div class="member-photo" role="img" aria-label="Portrait of a team member in a suit"></div><h3>ALIQUID EX EA</h3><p>Ut enim ad minima veniam</p><div class="member-social"><span></span><span></span><span></span></div></div>
    <div class="member"><div class="member-photo" role="img" aria-label="Portrait of a support team member with a headset"></div><h3>AD MINIMA</h3><p>Ut enim ad minima veniam</p><div class="member-social"><span></span><span></span><span></span></div></div>
    <div class="member"><div class="member-photo" role="img" aria-label="Portrait of a support team member with a headset"></div><h3>NEQUE PORRO</h3><p>Ut enim ad minima veniam</p><div class="member-social"><span></span><span></span><span></span></div></div>
  </div>
</section>

<svg class="footer-curve" width="1200" height="150" viewBox="0 0 1200 150">
  <path d="M0 150 L0 110 Q600 -20 1200 30 L1200 150Z" fill="#111"/>
  <path d="M0 104 Q600 -28 1200 22" stroke="#999" stroke-width="6" fill="none"/>
  <path d="M0 94 Q600 -40 1200 10" stroke="var(--blue)" stroke-width="10" fill="none"/>
</svg>

<footer class="site-footer">
  <div class="footer-brand"><span class="brand-dot"></span><span class="brand-name">Kestrel IT</span></div>
  <div class="footer-contact">
    <h4>CONTACT US</h4>
    <div class="call-here"><svg width="13" height="13" viewBox="0 0 24 24"><path d="M6.6 10.8a15 15 0 006.6 6.6l2.2-2.2c.3-.3.7-.4 1-.2 1.1.4 2.3.6 3.6.6.6 0 1 .4 1 1V20c0 .6-.4 1-1 1A17 17 0 013 4c0-.6.4-1 1-1h3.5c.6 0 1 .4 1 1 0 1.3.2 2.5.6 3.6.1.3 0 .7-.2 1z" fill="currentColor"/></svg>Call Us Here...</div>
    <div class="branches">
      <span>Main Number: 555-014-2280</span><span>Ashgrove: 555-014-5530</span>
      <span>Marlow Creek: 555-014-3310</span><span>Tarrin Falls: 555-014-6640</span>
      <span>Fenbury: 555-014-4420</span><span>Coldwater Bay: 555-014-7750</span>
    </div>
  </div>
  <div class="footer-follow">
    <h4>FOLLOW US</h4>
    <div class="follow-icons"><span></span><span></span><span></span></div>
  </div>
  <div class="subscribe">SUBSCRIBE NOW</div>
  <div class="copyright">© copyright 2017 Kestrel IT. All rights reserved &nbsp;|&nbsp; Terms &amp; Conditions &nbsp;|&nbsp; Privacy policy</div>
</footer>

</body>
</html>
```